Email mail merge - not a marketing email, this is an update email sent regularly to our members

HI I need a generic email designed to send out to our members, this is a tri-weekly (monday - updates - Wednesday - updates and Fridays - weekly round up.

we would like it to have within the mail body, 3 interactive, changeable boxes for example "quote of the week', 'top performer' and something else, It would be great if we can remove a box if and when we choose.
Our company is called Kr4ve Amusements or Kr4ve for short.
It needs to be in HTML to fit with our back office software.
We have all the logos for you already which I have included, I have also included our current email header.
our websites are...
kr4vamu.cub - This is our members back end site.
kr4vamu.com - This is our gaming site.
Please email me on derek@kr4vamu.com if you have any queries

Target Market(s)

All of our members - We currently have over 400 but it is growing at an astronomical rate.

Industry/Entity Type

Marketing

Font styles to use
Serif
Decorative
Script

Requirements
Must have
• At least two interactive, changeable boxes/areas that I can put photo's or quotes in to. I would also like some guidelines as to how I change these myself.
• The colours should be inline with our kr4vamu.club site.
Nice to have
• This is a positive email update so it needs to look clean and clear but vibrant, we are a unique company that is breaking records and is very successful.
• Our members have the ability and some already are earning vast sums of money.

```html
<!DOCTYPE html>
<html lang="en">
<head>
<meta charset="utf-8">
<title>Kr4ve Amusements – Member Update Email Layouts</title>
<link rel="stylesheet" href="https://fonts.googleapis.com/css2?family=Teko:wght@500;600&family=Josefin+Sans:wght@400;700&family=Gelasio:ital,wght@0,400;0,700;1,400&display=swap">
<style>
  :root {
    --teal: #3bbfad;
    --teal-text: #2fb3a0;
    --red: #d23a3a;
    --charcoal: #333333;
    --ink: #2b2b2b;
    --stage: #e3e3e3;
    --shell: #ebebeb;
    --placeholder: #a6a6a6;
    --brand-grey: #b9b9b9;
    --white: #ffffff;
  }
  * { box-sizing: border-box; margin: 0; padding: 0; }
  html, body { width: 1200px; height: 927px; overflow: hidden; }
  body {
    position: relative;
    background: linear-gradient(to bottom, var(--teal) 0 130px, var(--stage) 130px);
    font-family: "Gelasio", Georgia, serif;
    color: var(--ink);
  }

  .variant-label {
    position: absolute;
    top: 36px;
    width: 200px;
    text-align: center;
    font-family: "Teko", sans-serif;
    font-weight: 600;
    font-size: 54px;
    line-height: 1;
    letter-spacing: 2px;
    color: var(--charcoal);
  }
  .variant-label--a { left: 106px; }
  .variant-label--b { left: 490px; }
  .variant-label--c { left: 866px; }

  .email {
    position: absolute;
    top: 103px;
    width: 352px;
    border: 5px solid var(--white);
    background: var(--shell);
    box-shadow: 0 2px 6px rgba(0,0,0,.35);
  }
  .email--a { left: 40px; }
  .email--b { left: 419px; }
  .email--c { left: 798px; width: 354px; }

  /* Header */
  .email-header {
    position: relative;
    height: 150px;
    background: var(--charcoal);
  }
  .brand {
    position: absolute;
    top: 17px; left: 51px;
    font-family: "Josefin Sans", sans-serif;
    font-weight: 700;
    font-size: 15px;
    line-height: 1;
    color: var(--brand-grey);
  }
  .social {
    position: absolute;
    top: 20px; left: 210px;
    display: flex; gap: 6px;
  }
  .social span {
    width: 8px; height: 8px;
    border-radius: 50%;
    background: var(--teal);
  }
  .hero {
    position: absolute;
    left: 51px; top: 47px;
    width: 240px; height: 103px;
    background: var(--placeholder);
    border-radius: 8px 8px 0 0;
  }
  .hero-heading, .hero-subheading {
    position: absolute;
    right: 0;
    height: 15px;
    padding-right: 5px;
    font-family: "Teko", sans-serif;
    font-weight: 500;
    font-size: 12px;
    line-height: 16px;
    letter-spacing: 1px;
    text-align: right;
    color: var(--white);
    text-transform: uppercase;
  }
  .hero-heading { top: 72px; width: 166px; background: var(--teal); }
  .hero-subheading { top: 87px; width: 94px; background: var(--red); }

  /* Body */
  .email-body { padding: 0 51px; }
  .email--a .email-body { padding-bottom: 14px; }
  .email--b .email-body { padding-bottom: 6px; }
  .email--c .email-body { padding-bottom: 19px; }

  .letter {
    height: 192px;
    background: var(--white);
    padding: 7px 7px 0;
    font-size: 5.6px;
    line-height: 7.8px;
  }
  .letter p { margin-bottom: 6px; }
  .letter .greeting { font-weight: 700; margin-bottom: 8px; }
  .cta { color: var(--teal-text); font-weight: 700; }
  .signature {
    width: 42px; height: 20px;
    margin: -2px 0 2px;
    background: linear-gradient(135deg, #d9d9d9, #bfbfbf);
    border-radius: 2px;
  }
  .signer { margin-bottom: 0 !important; }
  .signer strong { display: block; }

  .story { background: var(--white); }
  .story-media {
    position: relative;
    background: var(--placeholder);
    display: flex; align-items: center; justify-content: center;
    font-family: "Josefin Sans", sans-serif;
    color: var(--white);
    letter-spacing: 1px;
  }
  .story--wide .story-media { height: 103px; font-size: 22px; }
  .story-copy {
    padding: 7px 7px 9px;
    font-size: 5.6px;
    line-height: 7.8px;
  }
  .story-title { color: var(--teal-text); font-family: "Josefin Sans", sans-serif; }

  .gap-3 { margin-top: 3px; } .gap-5 { margin-top: 5px; }
  .gap-8 { margin-top: 8px; } .gap-9 { margin-top: 9px; }

  .story-pair { display: flex; gap: 4px; height: 128px; }
  .story-pair .story { flex: 1; }
  .story-pair .story-media { height: 72px; font-size: 15px; }

  .ribbon { position: absolute; top: 0; right: 0; }

  .video .story-media { height: 105px; }
  .player-bar {
    position: absolute; left: 0; right: 0; bottom: 0;
    height: 13px;
  }

  /* Footer */
  .email-footer {
    background: var(--charcoal);
    padding: 0 51px 12px;
    text-align: center;
    color: var(--white);
    font-family: "Josefin Sans", sans-serif;
    font-size: 5.2px;
    line-height: 7.4px;
  }
  .footer-nav {
    display: flex; justify-content: space-around; align-items: center;
    height: 26px;
    background: var(--teal);
    font-weight: 700;
    font-size: 5.8px;
    margin-bottom: 14px;
  }
  .footer-notice { margin-top: 6px; }
  .footer-notice u { text-decoration: underline; }
</style>
</head>
<body>

<div class="variant-label variant-label--a">1-2</div>
<div class="variant-label variant-label--b">1-1</div>
<div class="variant-label variant-label--c">2-1</div>

<!-- Layout 1-2 -->
<section class="email email--a">
  <header class="email-header">
    <div class="brand">Kr4ve Amusements</div>
    <div class="social"><span></span><span></span><span></span><span></span><span></span><span></span></div>
    <div class="hero" role="img" aria-label="Header photograph">
      <div class="hero-heading">Heading text</div>
      <div class="hero-subheading">Subheading</div>
    </div>
  </header>
  <main class="email-body">
    <article class="letter">
      <p class="greeting">Hi Partner/Customer X,</p>
      <p>These first few months during pre-launch will throw us many challenges but as long as we continue to keep our integrity, I am confident that we will meet the expectations of our vision and aspirations to become one of <strong>the biggest, most profitable, affiliate rewards company</strong> in history...</p>
      <p>A very important task of the leaders of our company is to ensure that everyone within our organisation understands our strategy and to foster a culture that enables our team to implement this vision step by step.</p>
      <p>Just remember that we are <em>'the only Kr4ve in this space'</em>!</p>
      <p class="cta">This is a CALL TO ACTION link ▶</p>
      <p>Sincerely,</p>
      <div class="signature" role="img" aria-label="Handwritten signature"></div>
      <p class="signer"><strong>Derek Alan Morrow</strong>Chief Executive Officer of Kr4ve Amusements</p>
    </article>
    <article class="story story--wide gap-5">
      <div class="story-media" role="img" aria-label="Feature photograph">1 COLUMN</div>
      <p class="story-copy"><span class="story-title">Marketing prices/ INNOVATION WITH EFFICIENCY</span> "Our robust marketing team is always on the button, answering all your queries with great alacrity and helping you maximize the goodies on offer. <strong>They are not</strong> the typical parroting tele-representatives you'll generally find elsewhere; rather, they are honed and tuned to assist and aid your experience ]... ▶</p>
    </article>
    <div class="story-pair gap-9">
      <article class="story">
        <div class="story-media" role="img" aria-label="Feature photograph">2 COLUMNS</div>
        <p class="story-copy"><span class="story-title">PAID PLATFORM</span> "Did you know that millions of dollars are churned in a matter of days through <em>we invite you to be a part</em> of this epicenter of licensed betting <strong>Kr4ve</strong> . ]... ▶</p>
      </article>
      <article class="story">
        <div class="story-media" role="img" aria-label="Feature photograph">2 COLUMNS
          <svg class="ribbon" width="26" height="26" viewBox="0 0 26 26"><polygon points="0,0 26,0 26,26" fill="#d23a3a"/><polygon points="18,4 19.4,7.3 22.8,7.5 20.2,9.7 21,13 18,11.2 15,13 15.8,9.7 13.2,7.5 16.6,7.3" fill="#fff"/></svg>
        </div>
        <p class="story-copy"><span class="story-title">PROTECTED</span> "Did you know that millions of dollars are churned in a matter of days through <em>we invite you to be a part</em> of this epicenter of licensed betting <strong>Kr4ve</strong> . ]... ▶</p>
      </article>
    </div>
  </main>
  <footer class="email-footer">
    <nav class="footer-nav"><span>About us</span><span>Testimonials</span><span>Shop</span><span>Support</span><span>Contact</span></nav>
    <p><strong>© 2016 Kr4ve Amusements Ltd</strong></p>
    <p>Suite 4, Harbour Court Quay Road, Valmont, Northern Isles Territory</p>
    <p>Call: 1300 555 018 | Chat: kr4ve</p>
    <p class="footer-notice">You are receiving this email because you previously signed up for <strong>Kr4ve Amusements</strong>'s newsletter.<br>Don't want to receive emails from us? <u>Unsubscribe here.</u></p>
  </footer>
</section>

<!-- Layout 1-1 -->
<section class="email email--b">
  <header class="email-header">
    <div class="brand">Kr4ve Amusements</div>
    <div class="social"><span></span><span></span><span></span><span></span><span></span><span></span></div>
    <div class="hero" role="img" aria-label="Header photograph"></div>
  </header>
  <main class="email-body">
    <article class="letter">
      <p class="greeting">Hi Partner/Customer X,</p>
      <p>These first few months during pre-launch will throw us many challenges but as long as we continue to keep our integrity, I am confident that we will meet the expectations of our vision and aspirations to become one of <strong>the biggest, most profitable, affiliate rewards company</strong> in history...</p>
      <p>A very important task of the leaders of our company is to ensure that everyone within our organisation understands our strategy and to foster a culture that enables our team to implement this vision step by step.</p>
      <p>Just remember that we are <em>'the only Kr4ve in this space'</em>!</p>
      <p class="cta">This is a CALL TO ACTION link ▶</p>
      <p>Sincerely,</p>
      <div class="signature" role="img" aria-label="Handwritten signature"></div>
      <p class="signer"><strong>Derek Alan Morrow</strong>Chief Executive Officer of Kr4ve Amusements</p>
    </article>
    <article class="story story--wide gap-3">
      <div class="story-media" role="img" aria-label="Feature photograph"></div>
      <p class="story-copy"><span class="story-title">Marketing prices/ INNOVATION WITH EFFICIENCY</span> "Our robust marketing team is always on the button, answering all your queries with great alacrity and helping you maximize the goodies on offer. <strong>They are not</strong> the typical parroting tele-representatives you'll generally find elsewhere; rather, they are honed and tuned to assist and aid your experience ]... ▶</p>
    </article>
    <article class="story story--wide gap-5">
      <div class="story-media" role="img" aria-label="Feature photograph"></div>
      <p class="story-copy"><span class="story-title">Marketing prices/ INNOVATION WITH EFFICIENCY</span> "Our robust marketing team is always on the button, answering all your queries with great alacrity and helping you maximize the goodies on offer. <strong>They are not</strong> the typical parroting tele-representatives you'll generally find elsewhere; rather, they are honed and tuned to assist and aid your experience ]... ▶</p>
    </article>
  </main>
  <footer class="email-footer">
    <nav class="footer-nav"><span>About us</span><span>Testimonials</span><span>Shop</span><span>Support</span><span>Contact</span></nav>
    <p><strong>© 2016 Kr4ve Amusements Ltd</strong></p>
    <p>Suite 4, Harbour Court Quay Road, Valmont, Northern Isles Territory</p>
    <p>Call: 1300 555 018 | Chat: kr4ve</p>
    <p class="footer-notice">You are receiving this email because you previously signed up for <strong>Kr4ve Amusements</strong>'s newsletter.<br>Don't want to receive emails from us? <u>Unsubscribe here.</u></p>
  </footer>
</section>

<!-- Layout 2-1 -->
<section class="email email--c">
  <header class="email-header">
    <div class="brand">Kr4ve Amusements</div>
    <div class="social"><span></span><span></span><span></span><span></span><span></span><span></span></div>
    <div class="hero" role="img" aria-label="Header photograph"></div>
  </header>
  <main class="email-body">
    <article class="letter">
      <p class="greeting">Hi Partner/Customer X,</p>
      <p>These first few months during pre-launch will throw us many challenges but as long as we continue to keep our integrity, I am confident that we will meet the expectations of our vision and aspirations to become one of <strong>the biggest, most profitable, affiliate rewards company</strong> in history...</p>
      <p>A very important task of the leaders of our company is to ensure that everyone within our organisation understands our strategy and to foster a culture that enables our team to implement this vision step by step.</p>
      <p>Just remember that we are <em>'the only Kr4ve in this space'</em>!</p>
      <p class="cta">This is a CALL TO ACTION link ▶</p>
      <p>Sincerely,</p>
      <div class="signature" role="img" aria-label="Handwritten signature"></div>
      <p class="signer"><strong>Derek Alan Morrow</strong>Chief Executive Officer of Kr4ve Amusements</p>
    </article>
    <div class="story-pair gap-8">
      <article class="story">
        <div class="story-media" role="img" aria-label="Feature photograph"></div>
        <p class="story-copy"><span class="story-title">PAID PLATFORM</span> "Did you know that millions of dollars are churned in a matter of days through <em>we invite you to be a part</em> of this epicenter of licensed betting <strong>Kr4ve</strong> . ]... ▶</p>
      </article>
      <article class="story">
        <div class="story-media" role="img" aria-label="Feature photograph">
          <svg class="ribbon" width="26" height="26" viewBox="0 0 26 26"><polygon points="0,0 26,0 26,26" fill="#d23a3a"/><polygon points="18,4 19.4,7.3 22.8,7.5 20.2,9.7 21,13 18,11.2 15,13 15.8,9.7 13.2,7.5 16.6,7.3" fill="#fff"/></svg>
        </div>
        <p class="story-copy"><span class="story-title">PROTECTED</span> "Did you know that millions of dollars are churned in a matter of days through <em>we invite you to be a part</em> of this epicenter of licensed betting <strong>Kr4ve</strong> . ]... ▶</p>
      </article>
    </div>
    <article class="story video gap-5">
      <div class="story-media" role="img" aria-label="Video still">
        <svg width="44" height="44" viewBox="0 0 44 44"><circle cx="22" cy="22" r="19" fill="none" stroke="#fff" stroke-width="3"/><rect x="15" y="13" width="4" height="18" fill="#fff"/><rect x="25" y="13" width="4" height="18" fill="#fff"/></svg>
        <svg class="player-bar" width="240" height="13" viewBox="0 0 240 13">
          <rect width="240" height="13" fill="#2a2a2a"/>
          <circle cx="8" cy="6.5" r="4" fill="none" stroke="#fff" stroke-width="1"/>
          <polygon points="6.8,4.5 10,6.5 6.8,8.5" fill="#fff"/>
          <rect x="17" y="5.5" width="138" height="2" fill="#777"/>
          <rect x="17" y="5.5" width="76" height="2" fill="#d23a3a"/>
          <rect x="100" y="5.5" width="28" height="2" fill="#fff"/>
          <circle cx="93" cy="6.5" r="3" fill="#fff"/>
          <text x="161" y="8.5" font-size="5" fill="#fff" font-family="Josefin Sans, sans-serif">04:25</text>
          <polygon points="180,5 182,5 185,3 185,10 182,8 180,8" fill="#fff"/>
          <rect x="190" y="5.5" width="26" height="2" fill="#d23a3a"/>
          <rect x="216" y="4" width="3" height="5" fill="#fff"/>
          <path d="M226 4h3M226 4v3M236 4h-3M236 4v3M226 10h3M226 10v-3M236 10h-3M236 10v-3" stroke="#fff" stroke-width="1"/>
        </svg>
      </div>
      <p class="story-copy"><span class="story-title">Safe gaming experience / Kr4ve</span> "the Kr4ve experience is never enough to satiate their quest for gaming and betting. It is as if like we design a new altitude of fun and involvement every time. This is what drives all our users back to our platform each day ]... ▶</p>
    </article>
  </main>
  <footer class="email-footer">
    <nav class="footer-nav"><span>About us</span><span>Testimonials</span><span>Shop</span><span>Support</span><span>Contact</span></nav>
    <p><strong>© 2016 Kr4ve Amusements Ltd</strong></p>
    <p>Suite 4, Harbour Court Quay Road, Valmont, Northern Isles Territory</p>
    <p>Call: 1300 555 018 | Chat: kr4ve</p>
    <p class="footer-notice">You are receiving this email because you previously signed up for <strong>Kr4ve Amusements</strong>'s newsletter.<br>Don't want to receive emails from us? <u>Unsubscribe here.</u></p>
  </footer>
</section>

</body>
</html>
```